We need letterhead, Business Cards, and envelops designed. We have attached a design of our logo and a sample of letterhead idea that was started but never perfected, it is only an idea for the letterhead if you can design something better we may love that also we are open to change.
We want a design that looks professional in style. we are a non profit trade association in the construction industry. the green color in the attached design represent green building, and we like that. also if you just want to enhance the letterhead sample that we attached that would be fine also.
Thanks and good luck
also the name that should show on the first business cards should be Morgan Feltwick, Director are web address is www.pvtrn.org

```html
<!DOCTYPE html>
<html lang="en">
<head>
<meta charset="utf-8">
<title>PVTRN Business Card</title>
<link rel="stylesheet" href="https://fonts.googleapis.com/css2?family=Open+Sans:wght@400;600;700&display=swap">
<style>
  :root {
    --backdrop: #2a2a2a;
    --leaf: #9cc46a;
    --leaf-deep: #8ab85a;
    --leaf-mark: #6f9f3e;
    --paper: #ffffff;
    --paper-shade: #f2f2f2;
    --ink: #333333;
    --ink-soft: #555555;
  }
  * { margin: 0; padding: 0; box-sizing: border-box; }
  html, body {
    width: 1200px; height: 871px; overflow: hidden;
    background: var(--backdrop);
    font-family: "Open Sans", Arial, sans-serif;
  }
  .sheet {
    position: relative; width: 1200px; height: 871px;
    display: flex; align-items: center; justify-content: center; gap: 48px;
  }
  .card {
    position: relative; width: 520px; height: 297px;
    background: var(--paper); overflow: hidden;
  }
  .card__band {
    position: absolute; top: 0; left: 0; bottom: 0;
    background: linear-gradient(180deg, var(--leaf), var(--leaf-deep));
  }
  .card--back .card__band { width: 40%; }
  .card--front .card__band { width: 43%; }
  .card--front .card__panel {
    position: absolute; top: 0; right: 0; bottom: 0; width: 57%;
    background: linear-gradient(180deg, var(--paper), var(--paper-shade));
  }

  .brand { position: absolute; display: flex; align-items: center; gap: 10px; color: var(--ink); font-weight: 400; }
  .brand__mark { background: var(--leaf-mark); flex: none; }
  .brand__text { display: flex; flex-direction: column; line-height: 1; }
  .brand__short { letter-spacing: 2px; }

  .card--back .brand { left: 232px; top: 26px; }
  .card--back .brand__mark { width: 26px; height: 26px; }
  .card--back .brand__short { font-size: 44px; }
  .card--back .brand__long { font-size: 9px; margin-top: 5px; }

  .card--front .brand { left: 118px; top: 108px; }
  .card--front .brand__mark { width: 44px; height: 44px; }
  .card--front .brand__short { font-size: 76px; letter-spacing: 4px; }
  .card--front .brand__long { font-size: 14px; margin-top: 8px; }

  .contact {
    position: absolute; right: 26px; top: 112px; text-align: right; color: var(--ink);
  }
  .contact__name { font-size: 24px; font-weight: 400; line-height: 1.1; }
  .contact__role { font-size: 15px; font-weight: 700; margin-bottom: 18px; }
  .contact__line { font-size: 11px; color: var(--ink-soft); line-height: 1.45; text-transform: uppercase; }
  .contact__web { font-size: 11px; font-weight: 700; margin-top: 6px; }
</style>
</head>
<body>
<main class="sheet">
  <section class="card card--back" aria-label="Business card, details side">
    <div class="card__band"></div>
    <div class="brand">
      <span class="brand__mark"></span>
      <span class="brand__text">
        <span class="brand__short">PVTRN</span>
        <span class="brand__long">Pacific Valley Trade Registry Network</span>
      </span>
    </div>
    <div class="contact">
      <p class="contact__name">Morgan Feltwick</p>
      <p class="contact__role">Director</p>
      <p class="contact__line">Office Hours, 9:30 AM</p>
      <p class="contact__line">Map &amp; Directions</p>
      <p class="contact__line">(555) 014-2276</p>
      <p class="contact__web">www.pvtrn.org</p>
    </div>
  </section>

  <section class="card card--front" aria-label="Business card, brand side">
    <div class="card__band"></div>
    <div class="card__panel"></div>
    <div class="brand">
      <span class="brand__mark"></span>
      <span class="brand__text">
        <span class="brand__short">PVTRN</span>
        <span class="brand__long">Pacific Valley Trade Registry Network</span>
      </span>
    </div>
  </section>
</main>
</body>
</html>
```